Scented Candle Company Sticker Design for Packaging

We need a Sticker design for our various scented candle packages. Our handmade candles incorperate hand crafted Chiyogami Paper imported from Japan, which is wrapped around the jar. Each of the scents have different papers assigned to them and although we would like a general design in which the text can be changed according to each scent we would also like if the beautiful Japanese paper designs could be subtly incorporated in the design.

We want the the text of the sticker and logo of our company to be printed in gold foil once printed and our featured logo image is of a Dogwood tree. We think that perhaps the inclusion of dogwood blossom/s might look nice in the design but is not a must have!

We are fond of the delicate and classic print designs and etching designs. We would also like the design to be in a portrait rectangle that is closer in the shape of a square/ or not too long of a rectangle, and, would like to have a boarder on the edge of the sticker (this could incorporate the blossom if you wish, I have attached an image for reference/ inspiration) but we are after something much more simplistic and draws less attention to the eye and connected in the boarder.

Our brand is elegant and classic and we would like to be in keeping with our style. We have attached some images of the candles and our logo for inspiration, we do not want the stickers for the candle themselves but rather to place on the packaging.

Ive left some information for one of the candle scents for this design but once again I would like to reiterate that the design should allow for interchangeable titles for the other fragrances.

Coastal Fig Meadow(in smaller writing).
Coastal Fig Meadow, Orange blossom, cinnamon.

Our candles are hand made in Australia and a made from 100% soy wax and we would like to to be presented on the label.

I would like to mention again that we are looking for an elegant and classic design. We are looking for a simplistic design/layout that also focuses on the fine details. It should be striking but also not overbearing with an air of sophistication with minimal to no use of colours in encouraged.

I have also attached a font that is matched to the "candle co." underneath the tree in the logo.
Updates

I only just posted the design request, but first created the brief on the 2nd. I would like more time for the designers to both see my review and have an adequate amount of time to work on the project.

Target Market(s)

Up Market Shoppers.

Font styles to use
Script
Other font styles liked:
• Acorn

Colors
fbfbfb

Requirements
Must have
• Logo on the sticker.
Nice to have
• Nice to have a dogwood blossom incorporated into the boarder but must be simplistic as it doesn't want to be the main focus of the sticker
Should not have
• Photographs in the sticker design. Must be graphic design. No to little colour.

```html
<!DOCTYPE html>
<html lang="en">
<head>
<meta charset="utf-8">
<title>Ironbark Candle Co. – Coastal Fig Meadow Label</title>
<link rel="stylesheet" href="https://fonts.googleapis.com/css2?family=Josefin+Sans:wght@300;400&family=Marcellus&display=swap">
<style>
  :root {
    --ink: #000000;
    --paper: #fbfbfb;
    --ornament: #9a9a9a;
  }
  * { margin: 0; padding: 0; box-sizing: border-box; }
  html, body {
    width: 1200px;
    height: 1200px;
    overflow: hidden;
    background: var(--ink);
  }
  .canvas {
    position: relative;
    width: 1200px;
    height: 1200px;
    background: var(--ink);
  }
  .label {
    position: absolute;
    left: 217px;
    top: 217px;
    width: 764px;
    height: 764px;
    background: var(--paper);
  }
  .frame {
    position: absolute;
    left: 0;
    top: 0;
  }
  .corner-ornament {
    position: absolute;
    background: radial-gradient(circle at center, var(--ornament) 0%, #cfcfcf 70%, var(--paper) 100%);
    border-radius: 40%;
  }
  .corner-ornament--tl { left: 25px;  top: 32px;  width: 100px; height: 120px; }
  .corner-ornament--tr { left: 630px; top: 32px;  width: 115px; height: 120px; }
  .corner-ornament--bl { left: 25px;  top: 625px; width: 118px; height: 113px; }
  .corner-ornament--br { left: 625px; top: 625px; width: 120px; height: 113px; }

  .brand-mark {
    position: absolute;
    left: 337px;
    top: 178px;
    width: 90px;
    height: 90px;
    border-radius: 50%;
    background: var(--ink);
  }
  .brand-name {
    position: absolute;
    left: 0;
    width: 764px;
    text-align: center;
    font-family: "Marcellus", serif;
    font-weight: 400;
    color: var(--ink);
  }
  .brand-name__main {
    top: 322px;
    font-size: 78px;
    line-height: 1;
    letter-spacing: 0.13em;
    padding-left: 0.13em;
  }
  .brand-name__sub {
    top: 404px;
    font-size: 28px;
    line-height: 1;
    letter-spacing: 0.1em;
    padding-left: 0.1em;
  }

  .scent-banner {
    position: absolute;
    left: 148px;
    top: 473px;
    width: 470px;
    height: 55px;
  }
  .scent-banner__title {
    position: absolute;
    left: 0;
    top: 0;
    width: 470px;
    height: 55px;
    display: flex;
    align-items: center;
    justify-content: center;
    font-family: "Josefin Sans", sans-serif;
    font-weight: 300;
    font-size: 25px;
    letter-spacing: 0.05em;
    color: var(--paper);
    text-transform: uppercase;
    padding-top: 4px;
  }

  .product-facts {
    position: absolute;
    left: 0;
    top: 572px;
    width: 764px;
    text-align: center;
    font-family: "Josefin Sans", sans-serif;
    font-weight: 400;
    font-size: 19px;
    line-height: 29px;
    color: var(--ink);
    text-transform: uppercase;
  }
</style>
</head>
<body>
<main class="canvas">
  <section class="label">
    <svg class="frame" width="764" height="764" viewBox="0 0 764 764" aria-hidden="true">
      <g stroke="var(--ink)" stroke-width="3.5" fill="none">
        <line x1="149" y1="42" x2="620" y2="42"/>
        <line x1="163" y1="731" x2="607" y2="731"/>
        <line x1="28" y1="175" x2="28" y2="605"/>
        <line x1="741" y1="175" x2="741" y2="605"/>
      </g>
    </svg>

    <div class="corner-ornament corner-ornament--tl" role="img" aria-label="Corner spray of line-drawn blossoms"></div>
    <div class="corner-ornament corner-ornament--tr" role="img" aria-label="Corner spray of line-drawn blossoms"></div>
    <div class="corner-ornament corner-ornament--bl" role="img" aria-label="Corner spray of line-drawn blossoms"></div>
    <div class="corner-ornament corner-ornament--br" role="img" aria-label="Corner spray of line-drawn blossoms"></div>

    <div class="brand-mark" aria-hidden="true"></div>
    <p class="brand-name brand-name__main">IRONBARK</p>
    <p class="brand-name brand-name__sub">CANDLE CO.</p>

    <div class="scent-banner">
      <svg width="470" height="55" viewBox="0 0 470 55" aria-hidden="true">
        <polygon points="0,0 470,0 438,27.5 470,55 0,55 32,27.5" fill="var(--ink)"/>
      </svg>
      <h1 class="scent-banner__title">Coastal Fig Meadow</h1>
    </div>

    <p class="product-facts">100% Soy Wax<br>Made in Australia</p>
  </section>
</main>
</body>
</html>
```